Bright Ledger Bookkeeping Business Cards

I need Business Cards for a new Bookkeeping Business on the Gold Coast, Australia called "Bright Ledger Bookkeeping". I do Bookkeeping & BAS's for small to medium size businesses onsite (ie I am Mobile) or in house (at my office). I also do one on one Training onsite with clients.
I am a Registered BAS Agent, Accredited Partner with Tallyo & Member of the LEDGRA Bookkeeping Circle. The Logo's I have uploaded all need to be on a white background.

Target Market(s)

Small to Medium Size Businesses

Industry/Entity Type

Business

Contact Information for Business Card

Bright Ledger Bookkeeping
Kim Farrow
PO Box 562 Marlin Reach, Qld 4388
ph 0488 615 903
email kim@kimfarrow-example.com.au

Font styles to use
Other font styles liked:
• Maybe something like Bradley Hand ITC

Requirements
Must have
• All logo's attached on white background.
• Should state that I am a Registered BAS Agent.
Nice to have
• I have a tag - "Bright Ledger - Clear Sums" if you think that works please add.
Should not have
• No brown, green or yellow please.

```html
<!DOCTYPE html>
<html lang="en">
<head>
<meta charset="utf-8">
<title>Bright Ledger Bookkeeping – Business Cards</title>
<link rel="stylesheet" href="https://fonts.googleapis.com/css2?family=Handlee&display=swap">
<style>
  :root {
    --page-bg: #e9ebef;
    --card-white: #ffffff;
    --card-shade: #f1f2f4;
    --brand-blue: #3d6399;
    --rule-blue: #2e4f86;
    --badge-grey: #c9ced6;
    --ink: #151515;
    --hand: "Handlee", "Segoe Print", cursive;
  }
  * { box-sizing: border-box; margin: 0; padding: 0; }
  html, body { width: 1200px; height: 885px; overflow: hidden; }
  body {
    background: var(--page-bg);
    font-family: var(--hand);
    color: var(--ink);
    display: flex;
    align-items: center;
    justify-content: center;
    gap: 48px;
  }
  .card {
    position: relative;
    width: 530px;
    height: 324px;
    border-radius: 16px;
    background: linear-gradient(180deg, var(--card-white) 0%, var(--card-shade) 100%);
    box-shadow: 0 10px 28px rgba(20, 30, 50, 0.18);
    overflow: hidden;
  }
  .card__band {
    position: absolute;
    left: 0; right: 0; bottom: 0;
    height: 52px;
    background: var(--brand-blue);
  }
  /* front */
  .front__title {
    position: absolute;
    left: 34px; top: 36px;
    font-size: 40px;
    font-weight: 400;
    line-height: 1;
    white-space: nowrap;
  }
  .front__rule {
    position: absolute;
    left: 0; right: 0; top: 128px;
    height: 1px;
  }
  .front__rule::before, .front__rule::after {
    content: "";
    position: absolute;
    top: 0; height: 1px;
    background: var(--rule-blue);
  }
  .front__rule::before { left: 0; width: 250px; }
  .front__rule::after { left: 440px; right: 0; }
  .front__name {
    position: absolute;
    left: 262px; top: 110px;
    font-size: 30px;
    line-height: 1;
    white-space: nowrap;
  }
  .front__contact {
    position: absolute;
    left: 190px; top: 160px;
    list-style: none;
    font-size: 16px;
    line-height: 1.6;
    white-space: nowrap;
  }
  .front__credential {
    position: absolute;
    left: 34px; top: 164px;
    font-size: 15px;
    line-height: 1.3;
    width: 140px;
  }
  /* back */
  .back__title {
    position: absolute;
    left: 0; right: 0; top: 56px;
    text-align: center;
    font-size: 40px;
    font-weight: 400;
    line-height: 1;
    white-space: nowrap;
  }
  .back__tag {
    position: absolute;
    left: 0; right: 0; top: 112px;
    text-align: center;
    font-size: 18px;
  }
  .partners {
    position: absolute;
    left: 24px; right: 24px; top: 186px;
    display: flex;
    justify-content: space-between;
    align-items: center;
    list-style: none;
    font-size: 15px;
    white-space: nowrap;
  }
  .partner { display: flex; align-items: center; gap: 7px; }
  .partner__mark { width: 22px; height: 22px; background: var(--badge-grey); flex: none; }
  .partner__mark--circle { border-radius: 50%; }
</style>
</head>
<body>
  <section class="card card--front" aria-label="Business card front">
    <h1 class="front__title">Bright Ledger Bookkeeping</h1>
    <div class="front__rule"></div>
    <p class="front__name">Kim Farrow</p>
    <p class="front__credential">Registered BAS Agent</p>
    <ul class="front__contact">
      <li>0488 615 903</li>
      <li>kim@kimfarrow-example.com.au</li>
      <li>PO Box 562 Marlin Reach, Qld 4388</li>
    </ul>
    <div class="card__band"></div>
  </section>

  <section class="card card--back" aria-label="Business card back">
    <h2 class="back__title">Bright Ledger Bookkeeping</h2>
    <p class="back__tag">Bright Ledger - Clear Sums</p>
    <ul class="partners">
      <li class="partner"><span class="partner__mark" role="img" aria-label="Registered BAS Agent badge"></span>BAS Agent</li>
      <li class="partner"><span class="partner__mark"></span>Tallyo</li>
      <li class="partner"><span class="partner__mark partner__mark--circle"></span>LEDGRA Bookkeeping Circle</li>
    </ul>
    <div class="card__band"></div>
  </section>
</body>
</html>
```